Need webdesign for service company that provides Car hiring service and transit service

We need a web design for a company that provides airport transit services and transport services including Limo, Corporate cars, Disability transit, Family transit service. We need is a simple and professional design.

Below is site which we like and also offer the same service http://www.ridelarkway.com.au/
Updates

Project Deadline Extended
Reason: Waiting for the Feedback from multiple stakeholders. Need the time to select and approve the design

Target Market(s)

Tourism, Travel

Industry/Entity Type

Airport

Number of Pages Required

3 page

Font styles to use
Decorative
Script

Requirements
Must have
• Simple and Professional, Site we like http://www.ridelarkway.com.au/ and also need to mobile friendly
Should not have
• Shouldn't have too many images

```html
<!DOCTYPE html>
<html lang="en">
<head>
<meta charset="utf-8">
<title>Larkride – Private &amp; Business Transport</title>
<link rel="stylesheet" href="https://fonts.googleapis.com/css2?family=Bree+Serif&family=Poppins:wght@400;500;600&family=Roboto:wght@500&display=swap">
<style>
:root{
  --black:#000;
  --white:#fff;
  --ink:#1c1c1c;
  --muted:#6b6b6b;
  --band:#ececec;
  --panel:#3b3b3b;
  --field:#4d4d4d;
  --amber:#fbb731;
  --news:#f8b634;
}
*{box-sizing:border-box;margin:0;padding:0}
html,body{width:1200px;height:1035px;overflow:hidden;background:var(--white);font-family:'Poppins',sans-serif;color:var(--ink)}
.site-header{height:71px;background:var(--black);display:flex;align-items:center;justify-content:space-between;padding:0 99px}
.brand{display:flex;align-items:center;gap:10px;color:var(--white);font-family:'Poppins',sans-serif;font-weight:500;font-size:24px;letter-spacing:1px}
.brand-mark{width:30px;height:30px;border:2px solid var(--white)}
.header-tools{display:flex;gap:22px;align-items:center}
.header-tools svg{display:block}

.intro{text-align:center;padding-top:20px}
.intro h1{font-family:'Bree Serif',serif;font-weight:400;font-size:36px;letter-spacing:1px;line-height:1.1}
.intro h2{font-family:'Bree Serif',serif;font-weight:400;font-size:21px;letter-spacing:.6px;margin-top:9px}
.intro p{width:920px;margin:17px auto 0;font-size:11.2px;line-height:20.5px;color:var(--muted);text-align:justify;text-align-last:center}

.feature-grid{position:absolute;top:267px;left:148px;width:920px;height:361px}
.quote{position:absolute;left:0;top:0;width:297px;height:361px;background:linear-gradient(160deg,#3f3f3f,#333 60%,#2e2e2e);border-radius:3px;color:var(--white)}
.quote h3{font-weight:600;font-size:26px;text-align:center;margin-top:42px}
.field{position:absolute;left:19px;width:259px;height:31px;background:var(--field);display:flex;align-items:center;gap:8px;padding-left:11px;font-size:10.5px;color:#d6d6d6}
.field.origin{top:90px}.field.dest{top:134px}
.option{position:absolute;left:26px;display:flex;align-items:center;gap:12px;font-size:13px;font-weight:500}
.option.stops{top:181px}.option.vehicles{top:212px}
.estimate{position:absolute;left:23px;top:250px;width:249px;height:39px;background:var(--amber);color:var(--white);font-family:'Roboto',sans-serif;font-weight:500;font-size:22px;letter-spacing:.5px;display:flex;align-items:center;justify-content:center}
.note{position:absolute;left:24px;top:299px;font-size:10.5px}

.tile{position:absolute;overflow:hidden;border-radius:3px;display:flex;align-items:center;justify-content:center;color:var(--white);font-family:'Roboto',sans-serif;font-weight:500;font-size:25px}
.tile.member{left:309px;top:0;width:338px;height:175px;background:linear-gradient(120deg,#2a3442,#5b6d80 50%,#1f2835)}
.tile.contact{left:309px;top:186px;width:338px;height:175px;background:linear-gradient(135deg,#31475d,#5f7589 55%,#23313f)}
.tile.about{left:660px;top:0;width:259px;height:361px;background:linear-gradient(180deg,#c6c8cf,#8a7d74 35%,#3d2d24 70%,#7a79a0);align-items:flex-end;justify-content:flex-end;padding:0 15px 14px 0}

.benefits{position:absolute;top:658px;left:0;width:1200px;height:324px;background:var(--band)}
.benefit-row{position:absolute;top:25px;left:148px;width:920px;display:flex;justify-content:space-between}
.benefit{width:150px;text-align:center;font-size:11.2px;line-height:20.5px;color:var(--muted)}
.benefit svg{display:block;margin:0 auto 12px;height:22px}

.news{position:absolute;left:148px;top:144px;width:452px;height:154px;background:var(--news);color:var(--white);padding:21px 26px}
.news h4{font-weight:500;font-size:21px;letter-spacing:.4px}
.news p{font-weight:600;font-size:12px;line-height:20.5px;margin-top:9px}
.read-more{position:absolute;right:34px;bottom:11px;width:103px;height:27px;border:1px solid var(--white);border-radius:3px;font-size:12px;font-weight:600;display:flex;align-items:center;justify-content:center}

.payment{position:absolute;left:616px;top:144px;width:452px;height:154px;background:var(--black);color:var(--white);text-align:center}
.payment h4{font-weight:500;font-size:22px;margin-top:30px}
.cards{display:flex;justify-content:center;gap:9px;margin-top:22px}
.card{width:47px;height:30px;background:var(--white);border-radius:3px;color:var(--ink);font-size:8.5px;font-weight:600;display:flex;align-items:center;justify-content:center}

.site-footer{position:absolute;top:982px;left:0;width:1200px;height:53px;background:var(--black);color:var(--white);display:flex;align-items:center;justify-content:space-between;padding:0 99px}
.copyright{font-size:22px;margin-top:14px}
.footer-nav{display:flex;gap:27px;font-size:12px;font-weight:500;margin-top:-10px}
</style>
</head>
<body>
<header class="site-header">
  <div class="brand"><span class="brand-mark"></span>LARKRIDE</div>
  <nav class="header-tools" aria-label="Tools">
    <svg width="18" height="14" viewBox="0 0 18 14" fill="#fff"><rect width="18" height="2.6"/><rect y="5.7" width="18" height="2.6"/><rect y="11.4" width="18" height="2.6"/></svg>
    <svg width="18" height="18" viewBox="0 0 24 24" fill="#fff"><path d="M6.6 10.8a15.1 15.1 0 0 0 6.6 6.6l2.2-2.2c.3-.3.7-.4 1-.2 1.1.4 2.3.6 3.6.6.6 0 1 .4 1 1V20c0 .6-.4 1-1 1A17 17 0 0 1 3 4c0-.6.4-1 1-1h3.5c.6 0 1 .4 1 1 0 1.3.2 2.5.6 3.6.1.3 0 .7-.2 1z"/></svg>
    <svg width="18" height="18" viewBox="0 0 24 24" fill="none" stroke="#fff" stroke-width="3"><circle cx="10" cy="10" r="7"/><path d="M15 15l6 6" stroke-linecap="round"/></svg>
  </nav>
</header>

<section class="intro">
  <h1>Private &amp; Business</h1>
  <h2>Personalised Transport Service</h2>
  <p>Lorem Ipsum is simply dummy text of the printing and typesetting industry. Lorem Ipsum has been the industry's standard dummy text ever since the 1500s, when an unknown printer took a galley of type and scrambled it to make a type specimen book. It has survived not only five centuries, but also the leap into electronic typesetting, remaining essentially unchanged.Lorem Ipsum is simply dummy text of the printing and typesetting industry</p>
</section>

<section class="feature-grid">
  <form class="quote">
    <h3>Get Instant Quote</h3>
    <div class="field origin"><svg width="8" height="12" viewBox="0 0 8 12" fill="#fff"><circle cx="4" cy="4" r="3.5"/><rect x="3.2" y="6" width="1.6" height="6"/></svg>Origin (Public Location or Exact Address)</div>
    <div class="field dest"><svg width="8" height="12" viewBox="0 0 8 12" fill="none" stroke="#fff" stroke-width="1.4"><path d="M4 11.3C1.5 7.5.8 6 .8 4.2a3.2 3.2 0 0 1 6.4 0C7.2 6 6.5 7.5 4 11.3z"/><circle cx="4" cy="4.2" r="1"/></svg>Destination (Public Location or Exact Address)</div>
    <div class="option stops"><svg width="13" height="13" viewBox="0 0 13 13" fill="none" stroke="#fff" stroke-width="1.2"><rect x=".6" y=".6" width="11.8" height="11.8" rx="1.5"/><path d="M6.5 3.3v6.4M3.3 6.5h6.4"/></svg>ADD STOPS</div>
    <div class="option vehicles"><svg width="13" height="11" viewBox="0 0 13 11" fill="#fff"><rect width="13" height="2"/><rect y="4.5" width="13" height="2"/><rect y="9" width="13" height="2"/></svg>SHOW OTHER VEHICLES</div>
    <div class="estimate">ESTIMATE FARE</div>
    <div class="note">*See price guide for extras</div>
  </form>
  <a class="tile member" role="img" aria-label="Photo of business people shaking hands">Become A Member</a>
  <a class="tile contact" role="img" aria-label="Photo of hands signing a document">Contact Us Today</a>
  <a class="tile about" role="img" aria-label="Photo of two business people at a bright office window">About Larkride</a>
</section>

<section class="benefits">
  <div class="benefit-row">
    <div class="benefit"><svg viewBox="0 0 26 22" width="26" fill="#555"><rect x="1" y="5" width="24" height="16" rx="2"/><path d="M9 5V2h8v3" fill="none" stroke="#555" stroke-width="2"/><rect x="6" y="5" width="1.5" height="16" fill="#ececec"/><rect x="18.5" y="5" width="1.5" height="16" fill="#ececec"/></svg>Lorem Ipsum is simply dum my text of the printing and typesetting industry.</div>
    <div class="benefit"><svg viewBox="0 0 24 24" width="22" fill="none" stroke="#555" stroke-width="3"><circle cx="10" cy="10" r="7"/><path d="M15 15l6 6" stroke-linecap="round"/></svg>Lorem Ipsum is simply dum my text of the printing and typesetting industry.</div>
    <div class="benefit"><svg viewBox="0 0 26 22" width="26" fill="none" stroke="#555" stroke-width="2"><rect x="1" y="2" width="24" height="18" rx="1"/><path d="M1 8h24" stroke-width="3"/><path d="M4 15h5M11 15h3"/></svg>Lorem Ipsum is simply dum my text of the printing and typesetting industry.</div>
    <div class="benefit"><svg viewBox="0 0 28 22" width="28" fill="#555"><rect x="1" y="2" width="2" height="19"/><rect x="1" y="19" width="26" height="2"/><rect x="6" y="11" width="3" height="7"/><rect x="11" y="7" width="3" height="11"/><rect x="16" y="12" width="3" height="6"/><rect x="21" y="5" width="3" height="13"/></svg>Lorem Ipsum is simply dum my text of the printing and typesetting industry.</div>
    <div class="benefit"><svg viewBox="0 0 24 24" width="22" fill="none" stroke="#555" stroke-width="3"><path d="M4 4l16 16M20 4L4 20"/><path d="M2 9V2h7M15 2h7v7M22 15v7h-7M9 22H2v-7" stroke-width="2.5"/></svg>Lorem Ipsum is simply dum my text of the printing and typesetting industry.</div>
  </div>

  <article class="news">
    <h4>NEWS AND EVENTS</h4>
    <p>Lorem Ipsum is simply dummy text of the printing and typesetting in dustry. Lorem Ipsum has been the industry's standard dummy text ever since the 1500</p>
    <a class="read-more">Read More</a>
  </article>

  <div class="payment">
    <h4>Secure Online Payment</h4>
    <div class="cards">
      <span class="card">Paywell</span><span class="card">Bidmart</span><span class="card">Nimbus</span><span class="card">Vantra</span><span class="card">Dispay</span><span class="card">Mastra</span>
    </div>
  </div>
</section>

<footer class="site-footer">
  <div class="copyright">© Copyright 2017 - Larkride</div>
  <nav class="footer-nav"><span>Home</span><span>Sitemap</span><span>Privacy Policy</span><span>Terms &amp; Conditions</span></nav>
</footer>
</body>
</html>
```